Logo, Web and Mobile Designs for enterprise social media platform

All the details are in the attached document, please start reading the scope document first which explains what is this project about and the details about the needed deliverables, after that please read the UI_Requirements document which will detail what is expected regarding the coded web version since this is a coded contest, it is very important that you meet the UI requirements or suggest something else but we will need to agree first before working on the coded version

Good Luck

Target Market(s)

Enterprise Social Media

Industry/Entity Type

Media

Coding

Coded - Design and coding required

Number of Pages Required

5+ page

Font styles to use
Sans Serif

Requirements
Must have
• All the must haves are listed in the scope document so please check before you start

```html
<!DOCTYPE html>
<html lang="en">
<head>
<meta charset="utf-8">
<title>Teamora – Posts</title>
<link href="https://fonts.googleapis.com/css2?family=Roboto:wght@300;400;500&display=swap" rel="stylesheet">
<style>
:root{
  --bg:#ececec;
  --header:#f9f9f9;
  --line:#dcdcdc;
  --card:#ffffff;
  --ink:#333333;
  --muted:#555555;
  --accent:#2e7192;
  --brand:#2a9bd0;
  --orange:#f39c12;
  --footer:#1f88b6;
  --white:#ffffff;
}
*{box-sizing:border-box;margin:0;padding:0}
html,body{width:1200px;height:1041px;overflow:hidden}
body{background:var(--bg);font-family:'Roboto',sans-serif;color:var(--ink);position:relative}

.site-header{position:absolute;left:0;top:0;width:1200px;height:70px;background:var(--header);border-bottom:1px solid var(--line)}
.menu-toggle{position:absolute;left:0;top:0;width:145px;height:70px;border-right:1px solid #e6e6e6;display:flex;align-items:center;justify-content:center}
.brand{position:absolute;left:167px;top:16px;display:flex;align-items:center;gap:14px}
.brand-dot{width:36px;height:36px;border-radius:50%;background:var(--orange)}
.brand-name{font-size:30px;font-weight:400;color:var(--brand)}
.user{position:absolute;left:746px;top:18px;display:flex;align-items:center;gap:13px;font-size:17px;color:var(--muted);font-weight:300}
.avatar{width:34px;height:34px;border-radius:50%;background:radial-gradient(circle,#8a8a8a,#3a3a3a)}
.header-tool{position:absolute;top:0;height:70px;width:68px;border-left:1px solid #e6e6e6;display:flex;align-items:center;justify-content:center}
.badge{position:absolute;top:16px;min-width:20px;height:16px;border-radius:8px;font-size:11px;color:var(--white);text-align:center;line-height:16px;font-weight:500}
.badge.orange{background:var(--orange)}
.badge.blue{background:var(--brand)}

.post-grid{position:absolute;left:99px;top:103px;display:grid;grid-template-columns:486px 486px;column-gap:31px;row-gap:22px}
.post-card{position:relative;height:209px;background:var(--card);border:1px solid var(--line);box-shadow:0 1px 2px rgba(0,0,0,.04)}
.post-photo{position:absolute;left:9px;top:9px;width:183px;height:192px}
.post-body{position:absolute;left:218px;top:20px;width:250px}
.post-author{font-size:15.5px;font-weight:400;text-transform:uppercase;color:var(--ink);margin-left:-1px}
.post-title{margin-top:10px;font-size:16.5px;font-weight:400;color:var(--accent);line-height:21.5px}
.post-excerpt{margin-top:11px;font-size:11.3px;color:var(--muted);line-height:19.7px}
.read-more{display:inline-block;margin-top:12px;margin-left:-1px;font-size:12px;color:var(--ink);text-decoration:underline}
.post-actions{position:absolute;right:0;top:0;display:flex;border-left:1px solid var(--line);border-bottom:1px solid var(--line);background:#f7f7f7}
.post-actions span{width:33px;height:31px;display:flex;align-items:center;justify-content:center;border-right:1px solid var(--line)}
.post-actions span:last-child{border-right:none}

.pagination{position:absolute;top:823px;left:0;width:1200px;display:flex;justify-content:center;gap:9px}
.pagination span{height:26px;min-width:26px;padding:0 8px;background:var(--white);border:1px solid var(--line);font-size:12px;font-weight:500;color:#444;display:flex;align-items:center;justify-content:center}
.pagination .wide{padding:0 12px}

.site-footer{position:absolute;left:0;top:892px;width:1200px;height:149px;background:var(--footer);color:var(--white);text-align:center}
.social{position:absolute;top:28px;left:0;width:1200px;display:flex;justify-content:center;gap:13px}
.social span{width:24px;height:24px;border-radius:4px;background:var(--white)}
.footer-nav{position:absolute;top:71px;left:0;width:1200px;font-size:14.5px;font-weight:300}
.footer-nav i{font-style:normal;margin:0 9px}
.copyright{position:absolute;top:102px;left:0;width:1200px;font-size:14px}
</style>
</head>
<body>
<header class="site-header">
  <div class="menu-toggle">
    <svg width="18" height="14" viewBox="0 0 18 14"><rect y="0" width="18" height="2.6" fill="#888"/><rect y="5.7" width="18" height="2.6" fill="#888"/><rect y="11.4" width="18" height="2.6" fill="#888"/></svg>
  </div>
  <div class="brand"><span class="brand-dot"></span><span class="brand-name">Teamora</span></div>
  <div class="user"><span class="avatar" role="img" aria-label="User avatar photo"></span>Lerin Vasko
    <svg width="11" height="7" viewBox="0 0 11 7"><path d="M0 0h11L5.5 7z" fill="#555"/></svg>
  </div>
  <div class="header-tool" style="left:922px">
    <svg width="20" height="18" viewBox="0 0 20 18"><rect y="0" width="20" height="4" fill="#777"/><rect y="7" width="10" height="4" fill="#777"/><rect x="11" y="7" width="9" height="4" fill="#aaa"/><rect y="14" width="20" height="4" fill="#777"/></svg>
    <span class="badge orange" style="left:36px">8</span>
  </div>
  <div class="header-tool" style="left:990px">
    <svg width="20" height="20" viewBox="0 0 20 20"><circle cx="8" cy="8" r="6" fill="none" stroke="#666" stroke-width="2.6"/><path d="M12.5 12.5l6 6" stroke="#666" stroke-width="3" stroke-linecap="round"/></svg>
  </div>
  <div class="header-tool" style="left:1050px">
    <svg width="20" height="21" viewBox="0 0 20 21"><path d="M10 1c4 0 6 3 6 7v5l3 3H1l3-3V8c0-4 2-7 6-7z" fill="#666"/><circle cx="10" cy="18.5" r="2.3" fill="#666"/></svg>
    <span class="badge blue" style="left:30px">8</span>
  </div>
</header>

<main class="post-grid">
  <article class="post-card">
    <div class="post-photo" role="img" aria-label="Speaker in a blue suit presenting at a laptop before a conference audience" style="background:linear-gradient(135deg,#c25a2a,#5a2a3a 45%,#1c2e5c)"></div>
    <div class="post-body"><h3 class="post-author">Lerin Vasko</h3><h2 class="post-title">Nemo enim ipsam voluptatem quia voluptas sit</h2><p class="post-excerpt">Nulla at diam ornare, aliquam urna ve. Nam id risus a est luctus consectetur quis eget libero. Suspendisse potenti.</p><a class="read-more">READ MORE +</a></div>
    <div class="post-actions"><span><svg width="12" height="8" viewBox="0 0 12 8"><path d="M0 4q6-8 12 0q-6 8-12 0z" fill="#666"/><circle cx="6" cy="4" r="1.7" fill="#f7f7f7"/></svg></span><span><svg width="9" height="11" viewBox="0 0 9 11"><rect y="1" width="9" height="1.5" fill="#666"/><rect x="3" y="0" width="3" height="1.5" fill="#666"/><path d="M1 3h7l-.6 8H1.6z" fill="#666"/></svg></span><span><svg width="10" height="10" viewBox="0 0 10 10"><path d="M7 0l3 3-6 6-4 1 1-4z" fill="#666"/></svg></span></div>
  </article>
  <article class="post-card">
    <div class="post-photo" role="img" aria-label="Woman with glasses holding a microphone and tablet at an event" style="background:linear-gradient(135deg,#d9d6d2,#8aa3c4 50%,#6b5a56)"></div>
    <div class="post-body"><h3 class="post-author">Lerin Vasko</h3><h2 class="post-title">Nemo enim ipsam voluptatem quia voluptas sit</h2><p class="post-excerpt">Nulla at diam ornare, aliquam urna ve. Nam id risus a est luctus consectetur quis eget libero. Suspendisse potenti.</p><a class="read-more">READ MORE +</a></div>
    <div class="post-actions"><span><svg width="12" height="8" viewBox="0 0 12 8"><path d="M0 4q6-8 12 0q-6 8-12 0z" fill="#666"/><circle cx="6" cy="4" r="1.7" fill="#f7f7f7"/></svg></span><span><svg width="9" height="11" viewBox="0 0 9 11"><rect y="1" width="9" height="1.5" fill="#666"/><rect x="3" y="0" width="3" height="1.5" fill="#666"/><path d="M1 3h7l-.6 8H1.6z" fill="#666"/></svg></span><span><svg width="10" height="10" viewBox="0 0 10 10"><path d="M7 0l3 3-6 6-4 1 1-4z" fill="#666"/></svg></span></div>
  </article>
  <article class="post-card">
    <div class="post-photo" role="img" aria-label="Woman in a light blue shirt sitting on a desk in a bright office" style="background:linear-gradient(135deg,#ecebe8,#a9b8cc 55%,#5a4a40)"></div>
    <div class="post-body"><h3 class="post-author">Lerin Vasko</h3><h2 class="post-title">Nemo enim ipsam voluptatem quia voluptas sit</h2><p class="post-excerpt">Nulla at diam ornare, aliquam urna ve. Nam id risus a est luctus consectetur quis eget libero. Suspendisse potenti.</p><a class="read-more">READ MORE +</a></div>
    <div class="post-actions"><span><svg width="12" height="8" viewBox="0 0 12 8"><path d="M0 4q6-8 12 0q-6 8-12 0z" fill="#666"/><circle cx="6" cy="4" r="1.7" fill="#f7f7f7"/></svg></span><span><svg width="9" height="11" viewBox="0 0 9 11"><rect y="1" width="9" height="1.5" fill="#666"/><rect x="3" y="0" width="3" height="1.5" fill="#666"/><path d="M1 3h7l-.6 8H1.6z" fill="#666"/></svg></span><span><svg width="10" height="10" viewBox="0 0 10 10"><path d="M7 0l3 3-6 6-4 1 1-4z" fill="#666"/></svg></span></div>
  </article>
  <article class="post-card">
    <div class="post-photo" role="img" aria-label="Bearded man in a blue shirt working at a desk with charts" style="background:linear-gradient(135deg,#bcd0e2,#4f78a8 55%,#dde6ee)"></div>
    <div class="post-body"><h3 class="post-author">Lerin Vasko</h3><h2 class="post-title">Nemo enim ipsam voluptatem quia voluptas sit</h2><p class="post-excerpt">Nulla at diam ornare, aliquam urna ve. Nam id risus a est luctus consectetur quis eget libero. Suspendisse potenti.</p><a class="read-more">READ MORE +</a></div>
    <div class="post-actions"><span><svg width="12" height="8" viewBox="0 0 12 8"><path d="M0 4q6-8 12 0q-6 8-12 0z" fill="#666"/><circle cx="6" cy="4" r="1.7" fill="#f7f7f7"/></svg></span><span><svg width="9" height="11" viewBox="0 0 9 11"><rect y="1" width="9" height="1.5" fill="#666"/><rect x="3" y="0" width="3" height="1.5" fill="#666"/><path d="M1 3h7l-.6 8H1.6z" fill="#666"/></svg></span><span><svg width="10" height="10" viewBox="0 0 10 10"><path d="M7 0l3 3-6 6-4 1 1-4z" fill="#666"/></svg></span></div>
  </article>
  <article class="post-card">
    <div class="post-photo" role="img" aria-label="Smiling woman adjusting her glasses with a colleague at a laptop behind" style="background:linear-gradient(135deg,#7a4a34,#e8e2dc 50%,#7fa0c4)"></div>
    <div class="post-body"><h3 class="post-author">Lerin Vasko</h3><h2 class="post-title">Nemo enim ipsam voluptatem quia voluptas sit</h2><p class="post-excerpt">Nulla at diam ornare, aliquam urna ve. Nam id risus a est luctus consectetur quis eget libero. Suspendisse potenti.</p><a class="read-more">READ MORE +</a></div>
    <div class="post-actions"><span><svg width="12" height="8" viewBox="0 0 12 8"><path d="M0 4q6-8 12 0q-6 8-12 0z" fill="#666"/><circle cx="6" cy="4" r="1.7" fill="#f7f7f7"/></svg></span><span><svg width="9" height="11" viewBox="0 0 9 11"><rect y="1" width="9" height="1.5" fill="#666"/><rect x="3" y="0" width="3" height="1.5" fill="#666"/><path d="M1 3h7l-.6 8H1.6z" fill="#666"/></svg></span><span><svg width="10" height="10" viewBox="0 0 10 10"><path d="M7 0l3 3-6 6-4 1 1-4z" fill="#666"/></svg></span></div>
  </article>
  <article class="post-card">
    <div class="post-photo" role="img" aria-label="Man in a suit talking on the phone while typing on a laptop" style="background:linear-gradient(135deg,#d4dbe2,#8c98a6 50%,#3c3a3c)"></div>
    <div class="post-body"><h3 class="post-author">Lerin Vasko</h3><h2 class="post-title">Nemo enim ipsam voluptatem quia voluptas sit</h2><p class="post-excerpt">Nulla at diam ornare, aliquam urna ve. Nam id risus a est luctus consectetur quis eget libero. Suspendisse potenti.</p><a class="read-more">READ MORE +</a></div>
    <div class="post-actions"><span><svg width="12" height="8" viewBox="0 0 12 8"><path d="M0 4q6-8 12 0q-6 8-12 0z" fill="#666"/><circle cx="6" cy="4" r="1.7" fill="#f7f7f7"/></svg></span><span><svg width="9" height="11" viewBox="0 0 9 11"><rect y="1" width="9" height="1.5" fill="#666"/><rect x="3" y="0" width="3" height="1.5" fill="#666"/><path d="M1 3h7l-.6 8H1.6z" fill="#666"/></svg></span><span><svg width="10" height="10" viewBox="0 0 10 10"><path d="M7 0l3 3-6 6-4 1 1-4z" fill="#666"/></svg></span></div>
  </article>
</main>

<nav class="pagination">
  <span class="wide">Prev</span><span>1</span><span>2</span><span>3</span><span>4</span><span>5</span><span>6</span><span>…</span><span>22</span><span class="wide">Next</span>
</nav>

<footer class="site-footer">
  <div class="social"><span></span><span></span><span></span><span></span><span></span></div>
  <div class="footer-nav">Home<i>/</i>Contact<i>/</i>Topics<i>/</i>Posts and Comments<i>/</i>Discussion<i>/</i>Videos Links</div>
  <div class="copyright">Copyright @ 2015 - 2015.Teamora. All Rights Reserved.</div>
</footer>
</body>
</html>
```